Business card for medical clinic

I need an upmarket, modern medical/health business card for my clinic

Contact Information for Business Card

name, address, email, qr code

```html
<!DOCTYPE html>
<html lang="en">
<head>
<meta charset="utf-8">
<title>Solara Health Group – Business Card</title>
<link href="https://fonts.googleapis.com/css2?family=Cinzel:wght@500&family=Arimo:wght@400&display=swap" rel="stylesheet">
<style>
  :root {
    --backdrop: #3a3a3c;
    --navy-deep: #15244a;
    --navy: #1c3f77;
    --azure: #0aa3e0;
    --brand-blue: #1d8fd0;
    --white: #ffffff;
    --arc-grey: #8f8f95;
    --arc-navy: #1a2f5c;
  }
  html, body {
    margin: 0;
    width: 1200px;
    height: 689px;
    overflow: hidden;
    background: var(--backdrop);
  }
  .canvas {
    position: relative;
    width: 1200px;
    height: 689px;
  }
  .card {
    position: absolute;
    top: 190px;
    width: 540px;
    height: 309px;
    border-radius: 18px;
    overflow: hidden;
    box-shadow: 0 18px 40px rgba(0,0,0,.45);
  }
  .card-front {
    left: 40px;
    background: radial-gradient(ellipse 60% 70% at 55% 45%, var(--azure) 0%, var(--navy) 55%, var(--navy-deep) 100%);
  }
  .card-back { left: 620px; }
  .card-back .back-art { position: absolute; inset: 0; }

  .brand {
    position: absolute;
    display: flex;
    align-items: center;
    gap: 12px;
    font-family: "Cinzel", serif;
    font-weight: 500;
    letter-spacing: .06em;
    white-space: nowrap;
  }
  .brand-dot {
    border-radius: 50%;
    border: 2px solid currentColor;
    flex: none;
  }
  .brand-front {
    left: 0; right: 0; top: 0; bottom: 0;
    justify-content: center;
    color: #2a9fd8;
    font-size: 30px;
  }
  .brand-front .brand-dot { width: 58px; height: 58px; }
  .brand-back {
    left: 24px; top: 142px;
    gap: 8px;
    color: var(--brand-blue);
    font-size: 13px;
    letter-spacing: .04em;
  }
  .brand-back .brand-dot { width: 26px; height: 26px; }

  .holder {
    position: absolute;
    right: 26px; top: 30px;
    text-align: right;
    color: var(--white);
  }
  .holder-name {
    font-family: "Cinzel", serif;
    font-weight: 500;
    font-size: 22px;
    letter-spacing: .04em;
    margin: 0;
  }
  .holder-title {
    font-family: "Arimo", sans-serif;
    font-size: 11px;
    margin: 2px 0 0;
  }
  .contact {
    position: absolute;
    right: 26px; top: 150px;
    font-family: "Arimo", sans-serif;
    font-style: normal;
    font-size: 11.5px;
    line-height: 1.45;
    color: var(--white);
    text-align: right;
  }
  .contact p { margin: 0; }
  .contact .address { margin-bottom: 12px; }
  .contact-line {
    display: flex;
    justify-content: flex-end;
    align-items: center;
    gap: 7px;
  }
  .contact-line svg { width: 11px; height: 11px; flex: none; }
</style>
</head>
<body>
<main class="canvas">

  <section class="card card-front" aria-label="Card front">
    <div class="brand brand-front">
      <span class="brand-dot"></span>
      <span class="brand-name">Solara Health Group</span>
    </div>
  </section>

  <section class="card card-back" aria-label="Card back">
    <svg class="back-art" viewBox="0 0 540 309" preserveAspectRatio="none" aria-hidden="true">
      <defs>
        <radialGradient id="backGlow" cx="0.7" cy="0.4" r="0.55">
          <stop offset="0" stop-color="#0aa3e0"/>
          <stop offset="0.55" stop-color="#1c3f77"/>
          <stop offset="1" stop-color="#15244a"/>
        </radialGradient>
      </defs>
      <rect width="540" height="309" fill="url(#backGlow)"/>
      <path d="M0 0 H190 Q300 150 232 309 H0 Z" fill="#ffffff"/>
      <path d="M190 0 Q306 150 240 309" fill="none" stroke="#8f8f95" stroke-width="7"/>
      <path d="M204 0 Q318 150 252 309" fill="none" stroke="#1a2f5c" stroke-width="3"/>
    </svg>

    <div class="brand brand-back">
      <span class="brand-dot"></span>
      <span class="brand-name">Solara Health Group</span>
    </div>

    <header class="holder">
      <p class="holder-name">Daniel Hart</p>
      <p class="holder-title">President</p>
    </header>

    <address class="contact">
      <div class="address">
        <p>4120 Willow Crest Road</p>
        <p>Halden, Canada 51208</p>
      </div>
      <p class="contact-line">555-210-4837
        <svg viewBox="0 0 12 12"><path d="M2.5 1 L4.5 1 L5.3 3.5 L4 4.5 Q5 7 7.5 8 L8.5 6.7 L11 7.5 L11 9.5 Q10 11 8 10.8 Q2 9.5 1 3.5 Q1 1.8 2.5 1Z" fill="#fff"/></svg>
      </p>
      <p class="contact-line">555-318-9260
        <svg viewBox="0 0 12 12"><rect x="3" y="0.8" width="6" height="10.4" rx="1" fill="none" stroke="#fff" stroke-width="1.2"/><circle cx="6" cy="9.4" r=".6" fill="#fff"/></svg>
      </p>
      <p class="contact-line">info@solarahealth.com
        <svg viewBox="0 0 12 12"><rect x="0.8" y="2.5" width="10.4" height="7" fill="#fff"/><path d="M1 2.8 L6 6.6 L11 2.8" fill="none" stroke="#1c3f77" stroke-width="1"/></svg>
      </p>
      <p class="contact-line">www.solarahealth.com
        <svg viewBox="0 0 12 12"><circle cx="6" cy="6" r="5.2" fill="#fff"/><path d="M1 6 H11 M6 0.8 Q2.8 6 6 11.2 M6 0.8 Q9.2 6 6 11.2" fill="none" stroke="#1c3f77" stroke-width=".8"/></svg>
      </p>
    </address>
  </section>

</main>
</body>
</html>
```